I need a business card design for a new business based in South West Australia.
I specialize in residential window cleaning & general handyman maintenance.

Dale Marsh - 412 SILVER HAWK DETAILING
- Window Cleaning
- House Maintenance

```html
<!DOCTYPE html>
<html lang="en">
<head>
<meta charset="utf-8">
<title>Silver Hawk Detailing – Business Cards</title>
<link href="https://fonts.googleapis.com/css2?family=Open+Sans:wght@400;600&display=swap" rel="stylesheet">
<style>
  :root {
    --page-bg: #e9e9ea;
    --card-bg: #ffffff;
    --brand-blue: #1f5fae;
    --brand-orange: #f07a22;
    --text-grey: #555a60;
    --card-shadow: 0 18px 40px rgba(0,0,0,0.12), 0 2px 6px rgba(0,0,0,0.08);
  }
  * { box-sizing: border-box; margin: 0; padding: 0; }
  html, body {
    width: 1200px; height: 900px; overflow: hidden;
    background: var(--page-bg);
    font-family: "Open Sans", Arial, sans-serif;
  }
  .card-set {
    position: absolute; inset: 0;
    display: flex; align-items: center; justify-content: center; gap: 50px;
  }
  .card {
    position: relative;
    width: 525px; height: 300px;
    background: var(--card-bg);
    box-shadow: var(--card-shadow);
  }
  /* Name lockup: one colour, one weight, one plain circle */
  .brand { display: flex; align-items: center; gap: 10px; }
  .brand-dot {
    width: 26px; height: 26px; border-radius: 50%;
    background: var(--brand-orange); flex: none;
  }
  .brand-name {
    color: var(--brand-blue); font-weight: 600;
    font-size: 26px; white-space: nowrap;
  }
  /* Front */
  .card-front {
    display: flex; align-items: center; justify-content: center;
    border-top: 2px solid var(--brand-orange);
  }
  /* Back */
  .card-back { padding: 34px 36px; }
  .holder-name { color: var(--brand-blue); font-weight: 600; font-size: 17px; }
  .holder-title { color: var(--text-grey); font-size: 12px; margin-top: 1px; }
  .contact-list { list-style: none; margin-top: 36px; }
  .contact-item {
    display: flex; align-items: center; gap: 9px;
    color: var(--text-grey); font-size: 13px; line-height: 24px;
  }
  .contact-icon { width: 12px; height: 12px; fill: var(--brand-blue); flex: none; }
  .card-back .brand { position: absolute; right: 34px; bottom: 40px; gap: 8px; }
  .card-back .brand-dot { width: 18px; height: 18px; }
  .card-back .brand-name { font-size: 19px; }
</style>
</head>
<body>
<main class="card-set">
  <section class="card card-back" aria-label="Business card back">
    <h1 class="holder-name">Dale Marsh</h1>
    <p class="holder-title">Managing Director</p>
    <ul class="contact-list">
      <li class="contact-item">
        <svg class="contact-icon" viewBox="0 0 24 24"><path d="M6.6 10.8a15.1 15.1 0 0 0 6.6 6.6l2.2-2.2c.3-.3.7-.4 1-.2 1.1.4 2.3.6 3.6.6.6 0 1 .4 1 1V20c0 .6-.4 1-1 1A17 17 0 0 1 3 4c0-.6.4-1 1-1h3.5c.6 0 1 .4 1 1 0 1.2.2 2.4.6 3.6.1.3 0 .7-.2 1z"/></svg>
        044-987 654 321
      </li>
      <li class="contact-item">
        <svg class="contact-icon" viewBox="0 0 24 24"><path d="M2 5h20v14H2z M2 5l10 8 10-8" stroke="#fff" stroke-width="1.5"/></svg>
        hello@silverhawkwa.com
      </li>
      <li class="contact-item">
        <svg class="contact-icon" viewBox="0 0 24 24"><path d="M12 2a7 7 0 0 0-7 7c0 5.2 7 13 7 13s7-7.8 7-13a7 7 0 0 0-7-7zm0 9.5A2.5 2.5 0 1 1 12 6.5a2.5 2.5 0 0 1 0 5z"/></svg>
        18 Harbour Road, Bunbury WA
      </li>
    </ul>
    <div class="brand">
      <span class="brand-dot"></span><span class="brand-name">Silver Hawk Detailing</span>
    </div>
  </section>

  <section class="card card-front" aria-label="Business card front">
    <div class="brand">
      <span class="brand-dot"></span><span class="brand-name">Silver Hawk Detailing</span>
    </div>
  </section>
</main>
</body>
</html>
```